Velmora Systems Website

Website design for our company: Velmora Systems.
The website should look fresh and IT focused. Please have a look at http://www.velmorasystems.example.au/ for our current design. We want something fresh and new, professional looking, in WordPress so we can easily make changes.

It Company

```html
<!DOCTYPE html>
<html lang="en">
<head>
<meta charset="utf-8">
<title>Velmora Systems</title>
<link href="https://fonts.googleapis.com/css2?family=Open+Sans:ital,wght@0,400;0,600;0,700;1,700&display=swap" rel="stylesheet">
<style>
:root{
  --green:#00b159;
  --green-dark:#009a4d;
  --blue:#0c72c4;
  --mission-blue:#1a73b8;
  --topbar:#2f2f33;
  --dark:#333238;
  --quote:#5e5d62;
  --text:#444;
  --white:#fff;
}
*{box-sizing:border-box;margin:0;padding:0}
html,body{width:1200px;height:2338px;overflow:hidden}
body{font-family:"Open Sans",Arial,sans-serif;color:var(--text);background:var(--white)}
section,header{position:relative;width:1200px}
.topbar{height:39px;background:var(--topbar);color:#ddd;font-size:14px;text-align:center;line-height:39px}
.site-header{height:84px;background:var(--green);display:flex;align-items:center;padding:0 70px}
.brand{display:flex;align-items:center;gap:14px;color:var(--white);font-weight:700;font-size:26px}
.brand-dot{width:44px;height:44px;border-radius:50%;background:var(--white)}
.main-nav{margin-left:auto;display:flex;gap:28px}
.main-nav a{color:var(--white);text-decoration:none;font-weight:700;font-size:15px}
.hero{height:438px;background:linear-gradient(100deg,#1d2a3a 0%,#3e5670 35%,#8fa7bf 60%,#5d7b96 100%)}
.hero-photo{position:absolute;inset:0}
.search-panel{position:absolute;left:224px;top:275px;width:750px;height:134px;background:rgba(90,90,95,.75);border-radius:10px;padding:20px 24px}
.search-field{height:56px;background:var(--white);display:flex;align-items:center;padding:0 16px;font-size:27px;font-weight:700;color:#333}
.search-field svg{margin-left:auto}
.search-scope{display:flex;gap:40px;margin-top:16px;color:var(--white);font-size:14px;font-weight:700}
.search-scope span{display:flex;align-items:center;gap:10px}
.radio{width:20px;height:20px;border-radius:50%;background:var(--white);border:6px solid #555}
.radio.off{border:4px solid #ccc;background:#666}
.welcome{height:140px;background:var(--green);color:var(--white);text-align:center;padding-top:30px}
.welcome h1{font-size:27px;font-weight:700}
.welcome p{font-size:15.5px;margin-top:10px}
.mission{height:442px}
.mission-copy{position:absolute;left:99px;top:46px;width:570px}
.mission-copy h2{color:var(--mission-blue);font-size:26px;font-weight:700;margin-bottom:12px}
.mission-copy p{font-size:15.5px;line-height:21px;margin-bottom:18px}
.signature{display:flex;align-items:center;gap:20px;margin-top:10px}
.avatar{width:88px;height:88px;border-radius:50%;background:radial-gradient(circle,#b9967b,#5e4a3a)}
.signature p{font-style:italic;font-weight:700;font-size:15px;line-height:20px;margin:0}
.remote{position:absolute;left:707px;top:43px;width:425px;height:253px;color:var(--white);text-align:center}
.remote-photo{position:absolute;inset:0;background:linear-gradient(135deg,#7f8d99,#5b6a78 60%,#495663)}
.remote-body{position:relative;padding-top:24px}
.remote h3{font-size:26px;font-weight:700}
.code-input{margin:24px auto 0;width:356px;height:54px;background:#e6e6e6;border:4px solid #9ba3aa;text-align:left;padding:0 14px;line-height:46px;color:#666;font-size:14px;font-weight:600}
.connect{display:inline-block;margin-top:12px;background:var(--green);padding:11px 24px;border-radius:3px;font-weight:700;font-size:15px;border-bottom:3px solid var(--green-dark)}
.services{height:376px;background:var(--blue);color:var(--white);text-align:center}
.services h2{padding-top:36px;font-size:28px;font-weight:700}
.service{position:absolute;top:109px;width:280px;text-align:center}
.service-photo{width:172px;height:172px;border-radius:50%;border:3px solid var(--white);margin:0 auto}
.service p{margin-top:28px;font-weight:700;font-size:15px}
.arrow{position:absolute;top:154px}
.testimonials{height:532px;background:var(--dark);color:var(--white)}
.testimonials h2{text-align:center;padding-top:44px;font-size:27px;font-weight:700}
.quote{position:absolute;background:var(--quote);padding:24px 26px;font-size:15.5px;line-height:21.5px;border-radius:3px}
.quote p+p{margin-top:20px}
.quote::after{content:"";position:absolute;left:34px;bottom:-26px;border-left:26px solid var(--quote);border-bottom:26px solid transparent}
.quote-by{position:absolute;font-size:13px;color:#ddd}
.partners{height:287px;background:var(--green);color:var(--white);text-align:center}
.partners-intro{padding-top:48px;font-size:15.5px}
.vendor-row{display:flex;justify-content:center;gap:46px;margin-top:20px;font-weight:700;font-size:24px}
.vendor-row span{display:flex;align-items:center;gap:8px}
.vendor-mark{width:26px;height:26px;background:var(--white)}
.footer-rule{position:absolute;left:342px;top:220px;width:516px;height:1px;background:rgba(255,255,255,.3)}
.copyright{position:absolute;left:0;right:0;top:234px;font-size:13px;color:#d8f3e4}
</style>
</head>
<body>
<div class="topbar">Your IP address is 127.0.0.1 which resolves to xxx.yyy.xxx.255</div>
<header class="site-header">
  <div class="brand"><span class="brand-dot"></span>Velmora Systems</div>
  <nav class="main-nav"><a href="#">HOME</a><a href="#">CLIENTS</a><a href="#">SERVICES</a><a href="#">SUPPORT AREAS</a><a href="#">ABOUT US</a><a href="#">CONTACT US</a></nav>
</header>
<section class="hero">
  <div class="hero-photo" role="img" aria-label="Two IT engineers with a laptop in a server room"></div>
  <div class="search-panel">
    <div class="search-field">Search...
      <svg width="26" height="26" viewBox="0 0 26 26"><circle cx="10.5" cy="10.5" r="7.5" fill="none" stroke="#333" stroke-width="3.5"/><line x1="16" y1="16" x2="23" y2="23" stroke="#333" stroke-width="4" stroke-linecap="round"/></svg>
    </div>
    <div class="search-scope"><span><i class="radio"></i>LOCAL</span><span><i class="radio off"></i>WEB</span></div>
  </div>
</section>
<section class="welcome">
  <h1>Welcome to Velmora Systems</h1>
  <p>Velmora Systems is an Adelaide based company with a single objective - to excel in the support and service of all computer and IT needs.</p>
</section>
<section class="mission">
  <div class="mission-copy">
    <h2>Our Mission</h2>
    <p>We provide a high level of consulting services using the most experienced engineers at a reasonable and fair price. We believe in using a Business Value approach to every aspect of computer consulting to provide our clients with the most cost effective solutions.</p>
    <p>We strongly believe that we are in business with our clients. Each thing we do must be measured against our clients' business objectives. At the end of the day our client's success is our success.</p>
    <div class="signature">
      <div class="avatar" role="img" aria-label="Portrait of the managing director"></div>
      <p>Daniel Hart<br>Managing Director</p>
    </div>
  </div>
  <div class="remote">
    <div class="remote-photo" role="img" aria-label="Support agent with headset at a computer"></div>
    <div class="remote-body">
      <h3>Remote Support</h3>
      <div class="code-input">Enter your 6-digit code</div>
      <span class="connect">CONNECT NOW</span>
    </div>
  </div>
</section>
<section class="services">
  <h2>Our Services:</h2>
  <svg class="arrow" style="left:66px" width="22" height="96" viewBox="0 0 22 96"><polygon points="22,0 22,96 0,48" fill="#a9c9e6"/></svg>
  <div class="service" style="left:133px"><div class="service-photo" role="img" aria-label="Technicians working with network cabling" style="background:linear-gradient(135deg,#3d6fa8,#b9cde0)"></div><p>On-site Service</p></div>
  <div class="service" style="left:460px"><div class="service-photo" role="img" aria-label="Support agent with headset at a desk" style="background:linear-gradient(135deg,#dfe5ea,#9aa8b4)"></div><p>Remote Desktop Support</p></div>
  <div class="service" style="left:785px"><div class="service-photo" role="img" aria-label="Hand using a tablet computer" style="background:linear-gradient(135deg,#f2f2f2,#9b9b9b)"></div><p>Medical IT Service</p></div>
  <svg class="arrow" style="left:1112px" width="22" height="96" viewBox="0 0 22 96"><polygon points="0,0 0,96 22,48" fill="#a9c9e6"/></svg>
</section>
<section class="testimonials">
  <h2>What do our clients say about Velmora?</h2>
  <div class="quote" style="left:70px;top:121px;width:514px;height:322px">
    <p>“I have used Velmora Systems as a primary supplier of hardware &amp; computer support for the last 5 years, at both the Brannock &amp; Hale and the Corvell Pharmacy groups, where I have been employed as an I.T. Coordinator/Support Officer. Ravi &amp; his team are always friendly, prompt &amp; conscientious. They have an excellent wealth of knowledge &amp; I.T. savvy, always willing to ‘go the extra mile’ to get the job done.</p>
    <p>Their excellent knowledge of all POS systems is nice to know, to get you out of all sorts of problem situations. Not only that, someone is always contactable from Velmora Systems, no matter what time of the day.”</p>
  </div>
  <div class="quote-by" style="left:142px;top:462px">Liam Osterby B.Pharm, Greenway Chemists, Hillcrest</div>
  <div class="quote" style="left:617px;top:121px;width:515px;height:166px">
    <p>“I have always found the team extremely helpful with their advice over the phone. They also have the ability to access our computers remotely, and can rectify most problems quite swiftly. I have no hesitation in recommending Velmora Systems for all of your IT needs.”</p>
  </div>
  <div class="quote-by" style="left:696px;top:305px">Peter Lindqvist (Brannock &amp; Hale Pharmacy Group)</div>
</section>
<section class="partners">
  <p class="partners-intro">Velmora is proudly partnered with the following vendors:</p>
  <div class="vendor-row"><span><i class="vendor-mark"></i>Kestrel</span><span>Arcline</span><span>Norvato</span><span>Helix</span></div>
  <div class="vendor-row"><span>Quorra</span><span>Sentra</span></div>
  <div class="footer-rule"></div>
  <p class="copyright">Copyright © 2014 Velmora Systems Pty Ltd. All Rights Reserved.</p>
</section>
</body>
</html>
```